Halvery Construction Group Website

Need a dynamic corporate website that can be built on with time. We want to get our information out to the world and have a place where customers can submit requests for proposals.

Target Market(s)

Custom home owners and buyers. Architects and Real Estate Agents.

Industry/Entity Type

Construction

Number of Pages Required

3 page

Font styles to use
Serif
Sans Serif

Requirements
Must have
• Company logo, about, company contact information, biography, contact, projects,
• Sleek, modern, clean, attractive design.
• Online form customers can use for filling out a request for project proposal.
• Linkedin hyperlink.
• Uses www.halveryconstructiongroup.example

```html
<!DOCTYPE html>
<html lang="en">
<head>
<meta charset="utf-8">
<title>Halvery Construction Group</title>
<link rel="stylesheet" href="https://fonts.googleapis.com/css2?family=Montserrat:wght@400;600;700;800;900&family=Raleway:wght@400;500;600&display=swap">
<style>
:root{
  --blue:#0b4f9c;
  --blue-dark:#083d7c;
  --blue-light:#1d66bf;
  --ink:#333;
  --muted:#666;
  --grey-band:#e8e8e8;
  --footer:#1a1a1a;
  --white:#fff;
}
*{box-sizing:border-box;margin:0;padding:0}
html,body{width:1200px;height:2821px;overflow:hidden;background:var(--white)}
body{position:relative;font-family:'Raleway',sans-serif;color:var(--ink)}
.abs{position:absolute}
.heading{font-family:'Montserrat',sans-serif;font-weight:900;color:var(--blue);letter-spacing:.5px}
.btn{position:absolute;display:flex;align-items:center;justify-content:center;background:linear-gradient(var(--blue-light),var(--blue-dark));color:var(--white);font-family:'Montserrat',sans-serif;font-weight:700;text-transform:uppercase;letter-spacing:.5px}

/* header */
.site-header{position:absolute;left:0;top:0;width:1200px;height:158px;border-top:3px solid var(--blue);background:var(--white)}
.brand{position:absolute;left:132px;top:58px;display:flex;align-items:center;gap:12px;font-family:'Montserrat',sans-serif;font-weight:800;font-size:19px;color:var(--blue);white-space:nowrap}
.brand .mark{width:38px;height:38px;background:var(--blue);flex:none}
.contact-label{font-family:'Montserrat',sans-serif;font-size:11px;color:var(--muted);text-transform:uppercase;letter-spacing:.3px;white-space:nowrap}
.contact-value{font-family:'Montserrat',sans-serif;font-size:15px;font-weight:600;color:#222;display:flex;align-items:center;gap:10px;white-space:nowrap}
.header-divider{left:817px;top:30px;width:1px;height:50px;background:#ddd}
.main-nav{position:absolute;top:114px;left:0;width:1200px;font-family:'Montserrat',sans-serif;font-size:12px;font-weight:600;color:#555;text-transform:uppercase}
.main-nav span{position:absolute}
.main-nav .active{color:var(--blue)}

/* hero */
.hero{left:0;top:158px;width:1200px;height:478px;background:linear-gradient(180deg,#a9c6d2 0%,#c6d6d6 45%,#b69a6c 85%,#7e6a4e 100%)}
.hero-title{left:0;top:272px;width:1200px;text-align:center;font-family:'Montserrat',sans-serif;font-weight:900;font-size:47px;color:var(--white);text-shadow:0 2px 6px rgba(0,0,0,.35)}
.hero-sub{left:0;top:360px;width:1200px;text-align:center;font-family:'Montserrat',sans-serif;font-weight:600;font-size:15px;color:var(--white);text-transform:uppercase;text-shadow:0 1px 4px rgba(0,0,0,.4)}
.dots{left:592px;top:588px;display:flex;gap:8px}
.dots i{width:10px;height:10px;border-radius:50%;background:var(--blue)}

/* about */
.about-title{left:510px;top:688px;font-size:34px}
.body-copy{font-size:12.5px;line-height:24px;color:#555}

/* portfolio */
.portfolio{left:0;top:1048px;width:1200px;height:829px;background:var(--grey-band)}
.section-title{left:0;width:1200px;text-align:center;font-size:34px}
.card{position:absolute;width:297px;height:228px;background:var(--white);padding:5px;box-shadow:0 1px 3px rgba(0,0,0,.15)}
.card .photo{width:100%;height:100%}
.card.featured .photo{background:linear-gradient(135deg,#2a6cc0,#0d4f9e);display:flex;flex-direction:column;align-items:center;justify-content:center;color:var(--white)}
.card.featured h3{font-family:'Montserrat',sans-serif;font-weight:700;font-size:20px}
.card.featured p{font-size:12px;margin-top:8px}

/* contact */
.field{position:absolute;border:1px solid #d6d6d6;border-radius:3px;font-size:12px;color:#666;padding:13px 10px}
.info-title{font-family:'Montserrat',sans-serif;font-weight:800;font-size:20px;color:var(--blue)}
.info-line{font-size:12px;line-height:20px;color:#555;display:flex;gap:12px;align-items:flex-start}

/* footer */
.site-footer{left:0;top:2417px;width:1200px;height:404px;background:var(--footer)}
.footer-brand{position:absolute;left:132px;top:2500px;display:flex;align-items:center;gap:12px;font-family:'Montserrat',sans-serif;font-weight:800;font-size:19px;color:var(--white);white-space:nowrap}
.footer-brand .mark{width:38px;height:38px;background:var(--white);flex:none}
.footer-text{font-size:12px;line-height:20px;color:#ddd}
.footer-heading{font-family:'Montserrat',sans-serif;font-weight:700;font-size:14px;letter-spacing:.3px;color:var(--white)}
.quick-links{list-style:none;font-size:12px;line-height:19px;color:#ddd}
.social{display:flex;gap:22px}
.social i{width:14px;height:14px;border-radius:50%;background:var(--white)}
.thumb{position:absolute;width:70px;height:62px}
.footer-rule{left:132px;top:2760px;width:935px;height:1px;background:#3a3a3a}
.copyright{left:0;top:2780px;width:1200px;text-align:center;font-size:11.5px;color:#ccc}
</style>
</head>
<body>

<header class="site-header">
  <div class="brand"><span class="mark"></span>Halvery Construction Group</div>
  <div class="abs contact-label" style="left:609px;top:33px">Have a question? Call us now</div>
  <div class="abs contact-value" style="left:612px;top:58px">
    <svg width="13" height="13" viewBox="0 0 24 24"><path fill="#0b4f9c" d="M6.6 10.8a15 15 0 006.6 6.6l2.2-2.2a1 1 0 011-.25 11.4 11.4 0 003.6.57 1 1 0 011 1V20a1 1 0 01-1 1A17 17 0 013 4a1 1 0 011-1h3.5a1 1 0 011 1c0 1.25.2 2.45.57 3.57a1 1 0 01-.25 1z"/></svg>1800-555-0142</div>
  <div class="abs header-divider"></div>
  <div class="abs contact-label" style="left:850px;top:33px">Need support? Drop us an email</div>
  <div class="abs contact-value" style="left:852px;top:58px">
    <svg width="14" height="12" viewBox="0 0 24 20"><rect x="1" y="1" width="22" height="18" fill="none" stroke="#0b4f9c" stroke-width="2"/><path d="M1 2l11 9 11-9" fill="none" stroke="#0b4f9c" stroke-width="2"/></svg>info@halveryconstruction.example</div>
  <nav class="main-nav">
    <span class="active" style="left:681px">Home</span>
    <span style="left:752px">About us</span>
    <span style="left:848px">Bio</span>
    <span style="left:903px">Projects</span>
    <span style="left:997px">Contact us</span>
  </nav>
</header>

<section>
  <div class="abs hero" role="img" aria-label="Construction site with tower cranes, tablet showing skyscrapers, yellow hard hat and blueprints"></div>
  <h1 class="abs hero-title">HALVERY CONSTRUCTION</h1>
  <p class="abs hero-sub">Neque porro quisquam est qui dolorem ipsum quia dolor sit amet, consectetur, adipisci velit..</p>
  <div class="btn" style="left:498px;top:421px;width:205px;height:53px;font-size:15px">Request quote</div>
  <div class="abs dots"><i></i></div>
</section>

<section>
  <svg class="abs" style="left:132px;top:673px" width="314" height="337" viewBox="0 0 314 337" role="img" aria-label="Construction worker in a yellow hard hat holding a tablet">
    <defs>
      <linearGradient id="workerTone" x1="0" y1="0" x2="0" y2="1">
        <stop offset="0" stop-color="#e8c34a"/>
        <stop offset=".25" stop-color="#c9a489"/>
        <stop offset=".5" stop-color="#5c7f9e"/>
        <stop offset="1" stop-color="#4d6f8c"/>
      </linearGradient>
    </defs>
    <polygon points="157,4 310,88 310,249 157,333 4,249 4,88" fill="#2b2b2b"/>
    <polygon points="157,24 292,98 292,239 157,313 22,239 22,98" fill="url(#workerTone)"/>
  </svg>
  <h2 class="abs heading about-title">ABOUT US</h2>
  <p class="abs body-copy" style="left:510px;top:746px;width:560px">Lorem ipsum dolor sit amet, consectetur adipiscing elit, sed do eiusmod tempor incididunt ut labore et dolore magna aliqua.</p>
  <p class="abs body-copy" style="left:510px;top:816px;width:560px">Nemo enim ipsam voluptatem quia voluptas sit aspernatur aut odit aut fugit, sed quia consequuntur magni dolores eos qui ratione voluptatem sequi nesciunt. Neque porro quisquam est, qui dolorem ipsum quia dolor sit amet, consectetur, adipisci velit, sed quia non numquam eius modi tempora incidunt ut labore et dolore magnam aliquam quaerat voluptatem.</p>
  <div class="btn" style="left:510px;top:937px;width:130px;height:39px;font-size:11px">Read more</div>
</section>

<section>
  <div class="abs portfolio"></div>
  <h2 class="abs heading section-title" style="top:1110px">PORTFOLIO</h2>
  <div class="card featured" style="left:131px;top:1226px"><div class="photo"><h3>OFFICE RENOVATION</h3><p>Sydney, Australia</p></div></div>
  <div class="card" style="left:454px;top:1226px"><div class="photo" role="img" aria-label="Two engineers reviewing plans beside a crane" style="background:linear-gradient(180deg,#9fc0e0,#dfe6ee 55%,#777 100%)"></div></div>
  <div class="card" style="left:776px;top:1226px"><div class="photo" role="img" aria-label="City towers under construction at sunset" style="background:linear-gradient(160deg,#f0d29a,#8a8f9c 60%,#3f4a5c)"></div></div>
  <div class="card" style="left:131px;top:1484px"><div class="photo" role="img" aria-label="Glass high-rise with yellow tower cranes" style="background:linear-gradient(200deg,#3d8fe0,#7ab6ef 60%,#4a5b6e)"></div></div>
  <div class="card" style="left:454px;top:1484px"><div class="photo" role="img" aria-label="Blueprints with a hard hat and hammer" style="background:linear-gradient(135deg,#c9d7ea,#eef2f8 55%,#f0c234)"></div></div>
  <div class="card" style="left:776px;top:1484px"><div class="photo" role="img" aria-label="Site manager in a hard hat holding a tablet" style="background:linear-gradient(160deg,#e9c84a,#6f5f56 45%,#2b2b35)"></div></div>
  <div class="btn" style="left:542px;top:1757px;width:130px;height:39px;font-size:11px">View more</div>
</section>

<section>
  <h2 class="abs heading section-title" style="top:1955px">CONTACT US</h2>
  <div class="field" style="left:132px;top:2062px;width:295px;height:43px">Name</div>
  <div class="field" style="left:436px;top:2062px;width:294px;height:43px">Email</div>
  <div class="field" style="left:132px;top:2114px;width:598px;height:44px">Subject</div>
  <div class="field" style="left:132px;top:2165px;width:598px;height:139px">Message</div>
  <div class="btn" style="left:132px;top:2316px;width:171px;height:36px;font-size:14px;text-transform:none;border-radius:3px">Submit</div>

  <div class="abs info-title" style="left:760px;top:2058px">ADDRESS</div>
  <div class="abs info-line" style="left:760px;top:2099px;width:310px">
    <svg width="8" height="12" viewBox="0 0 12 18" style="margin-top:4px;flex:none"><path fill="#0b4f9c" d="M6 0a6 6 0 00-6 6c0 4.5 6 12 6 12s6-7.5 6-12a6 6 0 00-6-6zm0 8.5A2.5 2.5 0 116 3.5a2.5 2.5 0 010 5z"/></svg>
    <span>Lorem ipsum dolor sit amet, consectetur adipiscing elit, sed do eiusmod tempor incididunt</span></div>
  <div class="abs info-title" style="left:760px;top:2154px">PHONE</div>
  <div class="abs info-line" style="left:760px;top:2188px">
    <svg width="10" height="10" viewBox="0 0 24 24" style="margin-top:5px"><path fill="#0b4f9c" d="M6.6 10.8a15 15 0 006.6 6.6l2.2-2.2a1 1 0 011-.25 11.4 11.4 0 003.6.57 1 1 0 011 1V20a1 1 0 01-1 1A17 17 0 013 4a1 1 0 011-1h3.5a1 1 0 011 1c0 1.25.2 2.45.57 3.57a1 1 0 01-.25 1z"/></svg>
    <span>+25 62 5550 0190</span></div>
  <div class="abs info-title" style="left:760px;top:2218px">EMAIL</div>
  <div class="abs info-line" style="left:760px;top:2256px">
    <svg width="12" height="10" viewBox="0 0 24 20" style="margin-top:5px"><rect x="1" y="1" width="22" height="18" fill="none" stroke="#0b4f9c" stroke-width="2"/><path d="M1 2l11 9 11-9" fill="none" stroke="#0b4f9c" stroke-width="2"/></svg>
    <span>info@halveryconstruction.example</span></div>
</section>

<footer>
  <div class="abs site-footer"></div>
  <div class="footer-brand"><span class="mark"></span>Halvery Construction Group</div>
  <p class="abs footer-text" style="left:132px;top:2586px;width:290px">Lorem ipsum dolor sit amet, consectetur adipiscing elit, sed do eiusmod tempor incididunt ut labore et dolore magna aliqua.</p>
  <div class="abs social" style="left:132px;top:2684px" aria-label="Social links"><i></i><i></i><i></i><i></i></div>

  <div class="abs footer-heading" style="left:568px;top:2490px">QUICK LINKS</div>
  <ul class="abs quick-links" style="left:569px;top:2530px">
    <li>Home</li><li>About</li><li>Bio</li><li>Projects</li><li>Contact us</li>
  </ul>

  <div class="abs footer-heading" style="left:839px;top:2490px">INSTAGRAM</div>
  <div class="thumb" style="left:837px;top:2534px;background:linear-gradient(#7fa9d6,#8a6a45)" role="img" aria-label="Workers on site"></div>
  <div class="thumb" style="left:918px;top:2534px;background:linear-gradient(#6fa0d8,#d8a040)" role="img" aria-label="Worker in hard hat"></div>
  <div class="thumb" style="left:997px;top:2534px;background:linear-gradient(#a9c8e8,#c9b48a)" role="img" aria-label="Building under construction"></div>
  <div class="thumb" style="left:837px;top:2605px;background:linear-gradient(#5d7fa5,#c8a24a)" role="img" aria-label="Crane against the sky"></div>
  <div class="thumb" style="left:918px;top:2605px;background:linear-gradient(#e0b870,#6d5a44)" role="img" aria-label="Structure at dusk"></div>
  <div class="thumb" style="left:997px;top:2605px;background:linear-gradient(#c9d6ea,#f0c234)" role="img" aria-label="Plans and hard hat"></div>

  <div class="abs footer-rule"></div>
  <p class="abs copyright">© 2016 halveryconstructiongroup.example. All Rights Reserved</p>
</footer>

</body>
</html>
```